RESINE DENTAIRE ROSE box for dental resine pink to repair dentures broken

I will need a design for a box of pink dental resin. It is a pink dental resin which is intended for sale to individuals on Brindleway to repair or make small touch-ups or modifications to their dental prostheses. The title RESINE DENTAIRE ROSE must be clearly visible as well as the company logo. .I leave it to your creative mind to make an attractive and highly impactful and clearly visible sales design.
It is also necessary to make it clear to buyers through text or a vector image the purpose of the product: to repair a dental prosthesis.
Faible participation designers
Particulars who have need to repair their dentures

```html
<!DOCTYPE html>
<html lang="fr">
<head>
<meta charset="utf-8">
<title>Résine Dentaire Rose – Laboratoire Corvalis</title>
<link rel="stylesheet" href="https://fonts.googleapis.com/css2?family=Lato:wght@400;700&family=Noto+Serif:wght@700&display=swap">
<style>
  :root {
    --salmon: #e8806a;
    --salmon-light: #f2a996;
    --salmon-dark: #d96a55;
    --paper: #f4f4f4;
    --green: #6aa13a;
    --ink: #1e1e1e;
    --hazard: #e2541c;
    --stage: #ffffff;
  }
  * { margin: 0; padding: 0; box-sizing: border-box; }
  html, body { width: 1200px; height: 761px; overflow: hidden; background: var(--stage); }
  .canvas { position: relative; width: 1200px; height: 761px; font-family: "Lato", sans-serif; color: var(--ink); }

  .panel { position: absolute; background: var(--paper); overflow: hidden; box-shadow: 0 0 0 1px #e2e2e2; }
  .panel__band { position: absolute; inset: 0; width: 100%; height: 100%; }

  /* top panel */
  .panel--top { left: 380px; top: 70px; width: 600px; height: 150px; }
  .address { position: absolute; left: 118px; top: 22px; font-size: 12px; line-height: 1.25; letter-spacing: 0.04em; text-transform: uppercase; }
  .symbols { position: absolute; left: 118px; top: 108px; display: flex; gap: 8px; align-items: center; }
  .symbol-box { width: 22px; height: 16px; background: var(--hazard); }
  .symbol-mark { width: 22px; height: 16px; border: 1.5px solid var(--ink); border-radius: 3px; }

  /* front panel */
  .panel--front { left: 380px; top: 220px; width: 600px; height: 470px; }
  .brand { position: absolute; right: 32px; top: 36px; display: flex; align-items: center; gap: 10px; }
  .brand__square { width: 30px; height: 30px; background: var(--green); }
  .brand__name { font-weight: 700; font-size: 21px; line-height: 1.05; color: var(--green); letter-spacing: 0.04em; text-transform: uppercase; }
  .brand__since { font-weight: 700; font-size: 10px; color: var(--green); display: block; letter-spacing: 0.1em; }

  .title { position: absolute; right: 30px; top: 108px; text-align: right; font-family: "Noto Serif", serif; font-weight: 700; color: var(--salmon); font-size: 54px; line-height: 1; letter-spacing: 0.01em; }
  .title__shade { color: var(--salmon-dark); }

  .purpose { position: absolute; right: 34px; top: 282px; text-align: right; font-size: 15px; font-weight: 700; letter-spacing: 0.03em; color: var(--ink); }

  .shades { position: absolute; right: 34px; top: 318px; list-style: none; }
  .shade { display: flex; justify-content: flex-end; align-items: center; gap: 10px; font-size: 20px; letter-spacing: 0.03em; margin-bottom: 10px; }
  .shade__box { width: 30px; height: 30px; border: 2px solid var(--ink); background: #fff; display: flex; align-items: center; justify-content: center; }

  .illustration { position: absolute; left: 56px; top: 300px; width: 150px; height: 150px; border-radius: 50%; border: 3px solid var(--salmon); background: radial-gradient(circle at 50% 55%, #f3a5a5 0%, #f6c9c6 55%, #fbeeee 100%); }

  /* side panel */
  .panel--side { left: 230px; top: 220px; width: 150px; height: 470px; }
  .side-title { position: absolute; left: 18px; top: 30px; writing-mode: vertical-rl; font-family: "Noto Serif", serif; font-weight: 700; color: var(--salmon-dark); font-size: 44px; line-height: 0.95; }
  .side-brand { position: absolute; left: 100px; bottom: 30px; writing-mode: vertical-rl; display: flex; align-items: center; gap: 6px; }
  .side-brand__square { width: 14px; height: 14px; background: var(--green); }
  .side-brand__name { font-weight: 700; font-size: 12px; color: var(--green); letter-spacing: 0.06em; text-transform: uppercase; }
</style>
</head>
<body>
<main class="canvas">

  <section class="panel panel--top" aria-label="Dessus de la boîte">
    <svg class="panel__band" viewBox="0 0 600 150" preserveAspectRatio="none" aria-hidden="true">
      <path d="M0 0 H95 C70 50 70 100 85 150 H0 Z" fill="var(--salmon-light)"/>
    </svg>
    <p class="address">
      Laboratoire Corvalis<br>
      Villefranche B2<br>
      120 Allée des Tilleuls<br>
      06230 Villefranche Cedex 04<br>
      01 23 45 67 89
    </p>
    <div class="symbols">
      <svg width="22" height="18" viewBox="0 0 22 18" aria-label="Attention"><path d="M11 1 L21 17 H1 Z" fill="none" stroke="var(--ink)" stroke-width="1.6"/><path d="M11 6 V12 M11 14 V15.5" stroke="var(--ink)" stroke-width="1.6"/></svg>
      <span class="symbol-box" aria-hidden="true"></span>
      <span class="symbol-box" aria-hidden="true"></span>
      <span class="symbol-mark" aria-hidden="true"></span>
      <span class="symbol-mark" aria-hidden="true"></span>
      <span class="symbol-mark" aria-hidden="true"></span>
      <svg width="16" height="18" viewBox="0 0 16 18" aria-label="Date de péremption"><path d="M2 1 H14 L2 17 H14 Z" fill="none" stroke="var(--ink)" stroke-width="1.6"/></svg>
    </div>
  </section>

  <section class="panel panel--side" aria-label="Côté de la boîte">
    <svg class="panel__band" viewBox="0 0 150 470" preserveAspectRatio="none" aria-hidden="true">
      <rect width="150" height="470" fill="var(--salmon-light)"/>
      <path d="M90 0 H150 V470 H110 C80 330 80 150 90 0 Z" fill="var(--paper)"/>
    </svg>
    <h2 class="side-title">RÉSINE<br>DENTAIRE</h2>
    <div class="side-brand">
      <span class="side-brand__square" aria-hidden="true"></span>
      <span class="side-brand__name">Laboratoire Corvalis</span>
    </div>
  </section>

  <section class="panel panel--front" aria-label="Face avant de la boîte">
    <svg class="panel__band" viewBox="0 0 600 470" preserveAspectRatio="none" aria-hidden="true">
      <path d="M0 0 H95 C70 120 110 260 200 390 C220 420 230 450 235 470 H0 Z" fill="var(--salmon-light)"/>
      <path d="M60 0 C45 140 90 280 180 410 C195 430 205 450 210 470" fill="none" stroke="var(--salmon)" stroke-width="14" opacity="0.55"/>
    </svg>

    <div class="brand">
      <span class="brand__square" aria-hidden="true"></span>
      <span class="brand__name">Laboratoire<br>Corvalis <span class="brand__since">Depuis 1990</span></span>
    </div>

    <h1 class="title">RÉSINE<br>DENTAIRE<br><span class="title__shade">ROSE</span></h1>

    <p class="purpose">Pour réparer votre prothèse dentaire</p>

    <ul class="shades">
      <li class="shade">BLANCHE <span class="shade__box"></span></li>
      <li class="shade">ROSE <span class="shade__box"><svg width="26" height="26" viewBox="0 0 26 26" aria-label="coché"><path d="M4 13 L10 21 L23 3" fill="none" stroke="var(--ink)" stroke-width="4" stroke-linecap="round" stroke-linejoin="round"/></svg></span></li>
      <li class="shade">TRANSPERENTE <span class="shade__box"></span></li>
    </ul>

    <div class="illustration" role="img" aria-label="Illustration d'une prothèse dentaire avec gencive rose et dents blanches"></div>
  </section>

</main>
</body>
</html>
```